Company Values - print for wall

We ned a print of our values on one of the walls in our office. Create a couple of suggestions that we can print on our walls.

Summary:
- See power point with values
- make two suggestion: one with only titles + one with titles and bulletpoints / use the "We" version)
- make a suggestion in a galaxy raiders theme
- see brand book for inspiration
- see images of office for inspiration

The company's values that we want to highlight are: 1. Exceed expectations 2. Execute with passion 3. Empower each other Exceed expectations:​ • We establish a good understanding of current expectations.​ • We provide helpful, honest, and timely feedback.​ • We deliver impressive quality.​ Execute with passion:​ • We embrace change.​ • We seek innovative solutions.​ • We inspire others with your actions and attitudes. ​ • We care about success. ​ • We are confident and humble. Empower each other:​ • We are available to help colleagues.​ • We are open-minded.​ • We seek and share information proactively.​ • We respect others’ time.​ This is in line with achieving the company vision: « Our vision is to make a difference for our customers through our highly customizable solutions for planning, execution, and analysis. It’s less about the software itself and more about customer success. Make better decisions faster with Kelvanmark. »​ Bjarne Olav Tveit, CEO Kelvanmark Company slogan: Better Decisions Faster​ It's a lot of text above, but what we what to emphasize most are the following text above and here again: exceed expectations, execute with passion, empower each other We can do something fun and cool with the Galaxy Raiders theme as this is internal - that's the visual that would work with the company culture.

Font styles to use
Sans Serif

Requirements
Nice to have
• - one suggestion with Montserrat font
- one suggestion in galaxy raiders font

```html
<!DOCTYPE html>
<html lang="en">
<head>
<meta charset="utf-8">
<title>Kelvanmark – Core Values</title>
<link rel="stylesheet" href="https://fonts.googleapis.com/css2?family=Montserrat:wght@400;500;700;800&family=Russo+One&display=swap">
<style>
  :root {
    --backdrop: #cdcbc8;
    --space-deep: #0f0f2e;
    --space-mid: #26245a;
    --space-violet: #3a2f6e;
    --space-blue: #2c3f88;
    --accent-orange: #f0923a;
    --text-white: #ffffff;
    --saber-blue: #4a78ff;
    --saber-core: #dce6ff;
  }
  * { margin: 0; padding: 0; box-sizing: border-box; }
  html, body {
    width: 1200px; height: 2400px; overflow: hidden;
    background: var(--backdrop);
  }
  .poster {
    position: absolute; left: 50px; top: 420px;
    width: 1100px; height: 1560px; overflow: hidden;
    box-shadow: 0 20px 40px rgba(0,0,0,0.35);
    font-family: "Montserrat", sans-serif;
    color: var(--text-white);
  }
  .galaxy-backdrop {
    position: absolute; inset: 0;
    background:
      radial-gradient(ellipse 380px 300px at 70% 30%, rgba(110,100,190,0.45), transparent 70%),
      radial-gradient(ellipse 420px 360px at 25% 65%, rgba(80,60,150,0.45), transparent 70%),
      radial-gradient(ellipse 300px 260px at 85% 75%, rgba(90,110,200,0.35), transparent 70%),
      radial-gradient(ellipse 500px 400px at 50% 10%, rgba(60,70,160,0.4), transparent 70%),
      linear-gradient(160deg, var(--space-mid), var(--space-deep) 45%, var(--space-violet) 75%, var(--space-deep));
  }
  .brand-name {
    position: absolute; top: 62px; left: 0; width: 100%;
    text-align: center;
    font-weight: 800; font-size: 64px; letter-spacing: 1px;
    color: var(--text-white);
  }
  .title-vertical { position: absolute; left: 40px; top: 250px; width: 160px; height: 1070px; }
  .timeline { position: absolute; left: 195px; top: 250px; width: 160px; height: 960px; }
  .value {
    position: absolute; left: 370px; width: 700px;
  }
  .value-heading {
    font-family: "Russo One", sans-serif;
    color: var(--accent-orange);
    font-size: 37px; letter-spacing: 0.5px;
    text-transform: uppercase;
    margin-bottom: 4px;
  }
  .value-points { list-style: none; }
  .value-points li {
    position: relative; padding-left: 20px;
    font-size: 26px; font-weight: 500; line-height: 1.3;
    margin-bottom: 8px;
  }
  .value-points li::before {
    content: "•"; position: absolute; left: 0; top: 0;
  }
  .value-points.spaced li { margin-bottom: 13px; }
  .value--exceed { top: 318px; }
  .value--execute { top: 680px; }
  .value--empower { top: 1080px; }
  .contact-email {
    position: absolute; left: 0; width: 100%; top: 1450px;
    text-align: center; font-size: 31px; font-weight: 500; letter-spacing: 2px;
  }
</style>
</head>
<body>
  <main class="poster">
    <div class="galaxy-backdrop" role="img" aria-label="Deep space nebula with scattered stars in navy and violet tones"></div>

    <div class="brand-name">Kelvanmark</div>

    <svg class="title-vertical" viewBox="0 0 160 1070" aria-label="Core Values">
      <text transform="translate(140 1060) rotate(-90)" font-family="Montserrat, sans-serif" font-weight="800" font-size="140" textLength="1050" lengthAdjust="spacingAndGlyphs">
        <tspan fill="#f0923a">CORE </tspan><tspan fill="#ffffff">VALUES</tspan>
      </text>
    </svg>

    <svg class="timeline" viewBox="0 0 160 960" aria-hidden="true">
      <defs>
        <filter id="saber-glow" x="-200%" y="-10%" width="500%" height="120%">
          <feGaussianBlur stdDeviation="4" result="b"/>
          <feMerge><feMergeNode in="b"/><feMergeNode in="SourceGraphic"/></feMerge>
        </filter>
      </defs>
      <g filter="url(#saber-glow)">
        <line x1="80" y1="166" x2="80" y2="382" stroke="var(--saber-blue)" stroke-width="8"/>
        <line x1="80" y1="538" x2="80" y2="782" stroke="var(--saber-blue)" stroke-width="8"/>
        <line x1="80" y1="166" x2="80" y2="382" stroke="var(--saber-core)" stroke-width="2"/>
        <line x1="80" y1="538" x2="80" y2="782" stroke="var(--saber-core)" stroke-width="2"/>
      </g>
      <g fill="none" stroke="#fff" stroke-width="3">
        <circle cx="80" cy="88" r="76"/>
        <circle cx="80" cy="460" r="76"/>
        <circle cx="80" cy="860" r="76"/>
      </g>
      <!-- growth chart icon -->
      <g fill="#fff" stroke="#fff">
        <rect x="48" y="100" width="12" height="16" stroke="none"/>
        <rect x="66" y="90" width="12" height="26" stroke="none"/>
        <rect x="84" y="76" width="12" height="40" stroke="none"/>
        <line x1="40" y1="124" x2="120" y2="124" stroke-width="3"/>
        <polyline points="46,88 70,70 84,76 110,54" fill="none" stroke-width="3"/>
        <polyline points="98,54 110,54 110,66" fill="none" stroke-width="3"/>
      </g>
      <!-- gear icon -->
      <g fill="none" stroke="#fff" stroke-width="3">
        <circle cx="80" cy="460" r="24"/>
        <circle cx="80" cy="460" r="9"/>
        <g stroke-width="8" stroke-linecap="butt">
          <line x1="80" y1="426" x2="80" y2="434"/><line x1="80" y1="486" x2="80" y2="494"/>
          <line x1="46" y1="460" x2="54" y2="460"/><line x1="106" y1="460" x2="114" y2="460"/>
          <line x1="56" y1="436" x2="62" y2="442"/><line x1="98" y1="478" x2="104" y2="484"/>
          <line x1="104" y1="436" x2="98" y2="442"/><line x1="62" y1="478" x2="56" y2="484"/>
        </g>
      </g>
      <!-- empowerment icon: burst over raised hand block -->
      <g fill="none" stroke="#fff" stroke-width="3" stroke-linecap="round">
        <line x1="80" y1="818" x2="80" y2="834"/>
        <line x1="62" y1="824" x2="68" y2="838"/>
        <line x1="98" y1="824" x2="92" y2="838"/>
        <line x1="48" y1="836" x2="58" y2="846"/>
        <line x1="112" y1="836" x2="102" y2="846"/>
        <rect x="64" y="848" width="32" height="28" rx="6"/>
        <line x1="70" y1="876" x2="70" y2="896"/>
        <line x1="90" y1="876" x2="90" y2="896"/>
      </g>
    </svg>

    <section class="value value--exceed">
      <h2 class="value-heading">Exceed Expectations:</h2>
      <ul class="value-points spaced">
        <li>We establish a good understanding of current expectations.</li>
        <li>We provide helpful, honest, and timely feedback.</li>
        <li>We deliver impressive quality.</li>
      </ul>
    </section>

    <section class="value value--execute">
      <h2 class="value-heading">Execute with Passion:</h2>
      <ul class="value-points spaced">
        <li>We embrace change.</li>
        <li>We seek innovative solutions.</li>
        <li>We inspire others with your actions and attitudes.</li>
        <li>We care about success.</li>
        <li>We are confident and humble.</li>
      </ul>
    </section>

    <section class="value value--empower">
      <h2 class="value-heading">Empower Each Other:</h2>
      <ul class="value-points">
        <li>We are available to help colleagues.</li>
        <li>We are open-minded.</li>
        <li>We seek and share information proactively.</li>
        <li>We respect others’ time.</li>
      </ul>
    </section>

    <p class="contact-email">post@kelvanmark.com</p>
  </main>
</body>
</html>
```